Emergency Dental Referral Company

I need a brochure to advertise my business to prospective dentists that may want to join or to dentists that may want to use this for their own patients. I also need to advertise this brochure to ER physicians who see many dental emergencies. This brochure is meant to be dual purpose: advertise our company and services to the ER physicians who then hand out the brochures to the dental emergency patients in pain. See our website for further details at www.vellumcrestora.com

I will also be attaching our logo design.

Target Market(s)

Emergency Room physicians and other medical personnel who will distribute these brochures to patients in dental pain and dental emergencies

Industry/Entity Type

Business

Font styles to use
Serif
Sans Serif

Requirements
Must have
• Must be simple! Must have a call to action- inspiration to go to website. Highlight our guarantee that states "If you are not seen by a dentist in 24 hours or less, you will receive your money back. Emphasis on the logo. Must discuss how we find a dentist in your zip code in three easy steps.
• For the color- please make similar to our website of www.vellumcrestora.com
Nice to have
• Would like to state that this service can see patients at any hour of the day.
Should not have
• no contact information besides the URL. www.vellumcrestora.com

```html
<!DOCTYPE html>
<html lang="en">
<head>
<meta charset="utf-8">
<title>Your Emergency Dentist</title>
<link rel="stylesheet" href="https://fonts.googleapis.com/css2?family=Oswald:wght@300;400;500&family=Roboto:wght@400;500&display=swap">
<style>
  :root {
    --green: #3bb54b;
    --green-light: #48c257;
    --blue: #1b6fc2;
    --text-grey: #555a5f;
    --rule: #d9dde1;
    --white: #ffffff;
    --photo-steel: #a8a67c;
    --photo-steel-dark: #6f6e4e;
    --photo-hand: #b7897c;
    --photo-hand-dark: #7d6f9a;
    --photo-tools: #3d8fcb;
    --photo-tools-light: #e9e4cf;
  }
  html, body {
    margin: 0;
    padding: 0;
    width: 848px;
    height: 1200px;
    overflow: hidden;
    background: var(--white);
  }
  .brochure {
    position: relative;
    width: 848px;
    height: 1200px;
    overflow: hidden;
    background: var(--white);
  }
  .backdrop {
    position: absolute;
    inset: 0;
  }
  .wordmark {
    position: absolute;
    top: 34px;
    left: 0;
    width: 848px;
    display: flex;
    justify-content: center;
    align-items: center;
    gap: 10px;
    color: var(--white);
    font-family: "Oswald", "Arial Narrow", sans-serif;
    font-weight: 400;
    font-size: 22px;
    letter-spacing: 2px;
    text-transform: uppercase;
  }
  .wordmark-dot {
    width: 12px;
    height: 12px;
    border-radius: 50%;
    background: var(--white);
  }
  .headline {
    position: absolute;
    top: 112px;
    left: 0;
    width: 848px;
    margin: 0;
    text-align: center;
    color: var(--white);
    font-family: "Oswald", "Arial Narrow", sans-serif;
    font-weight: 300;
    font-size: 54px;
    line-height: 66px;
    text-transform: uppercase;
  }
  .headline strong {
    font-weight: 500;
    display: block;
  }
  .title {
    position: absolute;
    left: 86px;
    top: 838px;
    margin: 0;
    color: var(--blue);
    font-family: "Oswald", "Arial Narrow", sans-serif;
    text-transform: uppercase;
  }
  .title span { display: block; }
  .title .title-light {
    font-weight: 300;
    font-size: 66px;
    line-height: 80px;
  }
  .title .title-bold {
    font-weight: 500;
    font-size: 80px;
    line-height: 82px;
  }
  .mission {
    position: absolute;
    left: 496px;
    top: 842px;
    width: 250px;
    margin: 0;
    color: var(--text-grey);
    font-family: "Roboto", Arial, sans-serif;
    font-size: 15.6px;
    line-height: 30.6px;
    text-align: justify;
  }
  .steps {
    position: absolute;
    left: 86px;
    right: 86px;
    top: 1104px;
    margin: 0;
    padding: 12px 0 0;
    list-style: none;
    display: flex;
    justify-content: space-between;
    border-top: 1px solid var(--rule);
    color: var(--text-grey);
    font-family: "Roboto", Arial, sans-serif;
    font-size: 14px;
    line-height: 22px;
  }
  .steps li {
    display: flex;
    align-items: center;
    gap: 8px;
  }
  .step-number {
    width: 22px;
    height: 22px;
    border-radius: 50%;
    background: var(--green);
    color: var(--white);
    font-family: "Oswald", "Arial Narrow", sans-serif;
    font-weight: 500;
    font-size: 13px;
    text-align: center;
    line-height: 22px;
  }
  .call-to-action {
    position: absolute;
    left: 86px;
    right: 86px;
    top: 1148px;
    margin: 0;
    text-align: center;
    color: var(--blue);
    font-family: "Oswald", "Arial Narrow", sans-serif;
    font-weight: 400;
    font-size: 20px;
    line-height: 28px;
    letter-spacing: 0.5px;
  }
  .call-to-action span {
    color: var(--text-grey);
    font-weight: 300;
  }
</style>
</head>
<body>
<main class="brochure">
  <svg class="backdrop" width="848" height="1200" viewBox="0 0 848 1200">
    <defs>
      <radialGradient id="greenGlow" cx="50%" cy="20%" r="70%">
        <stop offset="0%" stop-color="var(--green-light)"/>
        <stop offset="100%" stop-color="var(--green)"/>
      </radialGradient>
      <linearGradient id="steelTone" x1="0" y1="0" x2="1" y2="1">
        <stop offset="0%" stop-color="var(--photo-steel)"/>
        <stop offset="100%" stop-color="var(--photo-steel-dark)"/>
      </linearGradient>
      <linearGradient id="handTone" x1="0" y1="0" x2="1" y2="1">
        <stop offset="0%" stop-color="var(--photo-hand-dark)"/>
        <stop offset="55%" stop-color="var(--photo-hand)"/>
        <stop offset="100%" stop-color="#c9c3d6"/>
      </linearGradient>
      <linearGradient id="toolsTone" x1="0" y1="0" x2="0" y2="1">
        <stop offset="0%" stop-color="var(--photo-tools-light)"/>
        <stop offset="100%" stop-color="var(--photo-tools)"/>
      </linearGradient>
    </defs>

    <polygon class="green-field" points="0,0 848,0 848,425 634,598 424,388 214,598 0,392" fill="url(#greenGlow)"/>

    <polygon class="photo-instruments" role="img" aria-label="Photo of stainless dental instruments on a tray"
             points="0,392 214,598 0,805" fill="url(#steelTone)"/>
    <polygon class="photo-hand" role="img" aria-label="Photo of an open hand holding a red pain-relief capsule"
             points="424,388 634,598 424,810 214,598" fill="url(#handTone)"/>
    <polygon class="photo-files" role="img" aria-label="Photo of colourful endodontic files standing in a blue holder"
             points="848,425 848,798 634,598" fill="url(#toolsTone)"/>
  </svg>

  <div class="wordmark"><span class="wordmark-dot"></span>Vellum Crestora</div>

  <h1 class="headline">Get seen within <strong>24 hours</strong> or your money back!</h1>

  <h2 class="title">
    <span class="title-light">Your</span>
    <span class="title-bold">Emergency</span>
    <span class="title-bold">Dentist</span>
  </h2>

  <p class="mission">Our mission plain and simple is to get you seen by a qualified dentist as quickly as possible to get you out of pain. Nobody likes pain and no one should have to live with it. If we can get you seen by a dentist in 24 hours or less, we have succeeded.</p>

  <ol class="steps">
    <li><span class="step-number">1</span>Enter your zip code</li>
    <li><span class="step-number">2</span>Pick a nearby dentist</li>
    <li><span class="step-number">3</span>Get seen, any hour</li>
  </ol>

  <p class="call-to-action"><span>Find your dentist now at</span> www.vellumcrestora.com</p>
</main>
</body>
</html>
```